Redesign of business card for Cedar Ridge Mechanical

We are looking for a new design for our business cards for Cedar Ridge Mechanical. We are a plumbing & HVAC construction company, operating on the West Coast of Canada and USA. Logo attached.
Industry/Entity Type
Construction - Plumbing & HVAC
Contact Information for Business Card
Name, address, phone numbers, email, website address
Look and feel
Each slider illustrates characteristics of the customer's brand and the style your logo design should communicate.

```html
<!DOCTYPE html>
<html lang="en">
<head>
<meta charset="utf-8">
<title>Cedar Ridge Mechanical – Business Card</title>
<link href="https://fonts.googleapis.com/css2?family=Montserrat:wght@400;700&display=swap" rel="stylesheet">
<style>
  :root {
    --page-bg: #1b1b1b;
    --card-dark: #242424;
    --card-light: #ffffff;
    --ink-dark: #1e1e1e;
    --ink-light: #ffffff;
    --ink-muted: #e6e6e6;
    --back-mark: #0c0c0c;
  }
  * { box-sizing: border-box; margin: 0; padding: 0; }
  html, body {
    width: 1200px; height: 1059px; overflow: hidden;
    background: var(--page-bg);
    font-family: "Montserrat", sans-serif;
  }
  .card {
    position: absolute;
    width: 693px; height: 393px;
    border-radius: 18px;
    overflow: hidden;
  }
  .card--front { left: 253px; top: 89px; background: var(--card-light); }
  .card--back { left: 253px; top: 546px; background: var(--card-dark); }

  .front-divider { position: absolute; inset: 0; width: 100%; height: 100%; }

  .brand {
    position: absolute; right: 89px; top: 112px;
    display: flex; align-items: center; gap: 8px;
    color: var(--ink-dark);
    font-weight: 700; font-size: 13px; letter-spacing: 0.04em;
    text-transform: uppercase;
  }
  .brand__square { width: 12px; height: 12px; background: var(--ink-dark); }

  .contact { position: absolute; left: 28px; top: 159px; color: var(--ink-light); }
  .contact__name { font-weight: 700; font-size: 22px; letter-spacing: 0.02em; line-height: 1; }
  .contact__title { font-size: 13.5px; color: var(--ink-muted); margin-top: 6px; letter-spacing: 0.02em; }
  .contact__address { font-size: 14px; line-height: 17.5px; margin-top: 29px; color: var(--ink-muted); }
  .contact__list { list-style: none; margin-top: 22px; }
  .contact__item {
    display: flex; align-items: center; gap: 11px;
    font-size: 14px; color: var(--ink-muted); height: 16px; margin-bottom: 11.5px;
  }
  .contact__icon { width: 15px; height: 15px; flex: none; }

  .back-brand {
    position: absolute; left: 0; right: 0; top: 196px;
    display: flex; align-items: center; justify-content: center; gap: 12px;
    color: var(--back-mark);
    font-weight: 700; font-size: 26px; letter-spacing: 0.04em; text-transform: uppercase;
  }
  .back-brand__square { width: 24px; height: 24px; background: var(--back-mark); }
</style>
</head>
<body>
  <section class="card card--front" aria-label="Business card front">
    <svg class="front-divider" viewBox="0 0 693 393" preserveAspectRatio="none" aria-hidden="true">
      <path fill="var(--card-dark)" d="M0,140 C120,120 260,150 380,200 C480,240 600,230 693,190 L693,393 L0,393 Z"/>
    </svg>

    <div class="brand">
      <span class="brand__square"></span>
      <span class="brand__name">Cedar Ridge Mechanical</span>
    </div>

    <div class="contact">
      <p class="contact__name">Daniel Brooks</p>
      <p class="contact__title">Managing Director</p>
      <p class="contact__address">240 Alder Creek Road<br>Salem, OR 97301</p>
      <ul class="contact__list">
        <li class="contact__item">
          <svg class="contact__icon" viewBox="0 0 24 24" aria-hidden="true"><path fill="#fff" d="M6.6 10.8a15 15 0 0 0 6.6 6.6l2.2-2.2a1 1 0 0 1 1-.25 11.4 11.4 0 0 0 3.6.57 1 1 0 0 1 1 1V20a1 1 0 0 1-1 1A17 17 0 0 1 3 4a1 1 0 0 1 1-1h3.5a1 1 0 0 1 1 1c0 1.25.2 2.45.57 3.570a1 1 0 0 1-.25 1z"/></svg>
          <span>555.204.7713</span>
        </li>
        <li class="contact__item">
          <svg class="contact__icon" viewBox="0 0 24 24" aria-hidden="true"><path fill="#fff" d="M3 5h18a1 1 0 0 1 1 1v12a1 1 0 0 1-1 1H3a1 1 0 0 1-1-1V6a1 1 0 0 1 1-1zm0 2v.4l9 5.6 9-5.6V7l-9 5.5z"/></svg>
          <span>info@cedarridgemechanical.com</span>
        </li>
        <li class="contact__item">
          <svg class="contact__icon" viewBox="0 0 24 24" aria-hidden="true"><circle cx="12" cy="12" r="9.5" fill="none" stroke="#fff" stroke-width="2"/><path fill="none" stroke="#fff" stroke-width="1.6" d="M2.5 12h19M12 2.5c3 3 3 16 0 19M12 2.5c-3 3-3 16 0 19"/></svg>
          <span>www.cedarridgemechanical.com</span>
        </li>
      </ul>
    </div>
  </section>

  <section class="card card--back" aria-label="Business card back">
    <div class="back-brand">
      <span class="back-brand__square"></span>
      <span class="back-brand__name">Cedar Ridge Mechanical</span>
    </div>
  </section>
</body>
</html>
```